New Business Card Design Project

Need a design that will create an impact / strong impression towards our clients for our business. We are in the lighting business and we do lighting retrofits for large commercial to industrial clientele.

Target Market(s)

Lighting Industry

Industry/Entity Type

Business

Font styles to use
Other font styles liked:
• we would like to use the font on our logo, not sure what it is though..

Requirements
Must have
• Our logo.
Nice to have
• We are open to suggestions that have to do with lighting.

```html
<!DOCTYPE html>
<html lang="en">
<head>
<meta charset="utf-8">
<title>Lumenway Retrofit Group – Business Card</title>
<link rel="stylesheet" href="https://fonts.googleapis.com/css2?family=Open+Sans:wght@400;600&family=Montserrat:wght@700&display=swap">
<style>
  :root {
    --forest: #1f4723;
    --leaf: #5fbf4a;
    --paper: #ffffff;
    --stage: #3a3a3a;
    --ink-light: #ffffff;
    --logo-green: #2f7a34;
  }
  * { margin: 0; padding: 0; box-sizing: border-box; }
  html, body { width: 1200px; height: 864px; overflow: hidden; }
  body {
    background: var(--stage);
    font-family: "Open Sans", Arial, sans-serif;
    position: relative;
  }
  .card {
    position: absolute;
    left: 280px;
    width: 640px;
    height: 366px;
    box-shadow: 0 10px 24px rgba(0,0,0,.45);
    overflow: hidden;
  }
  .card-front { top: 40px; background: var(--forest); }
  .card-back { top: 458px; background: var(--paper); display: flex; }

  .wordmark {
    display: flex; align-items: center; gap: 12px;
    font-family: "Montserrat", Arial, sans-serif;
    font-weight: 700; font-size: 34px; letter-spacing: .5px;
  }
  .wordmark-square { width: 22px; height: 22px; flex: none; }

  .card-front .wordmark {
    position: absolute; top: 130px; left: 0; right: 0;
    justify-content: center; color: var(--ink-light);
  }
  .card-front .wordmark-square { background: var(--ink-light); }
  .front-web {
    position: absolute; bottom: 42px; left: 0; right: 0;
    text-align: center; color: var(--ink-light); font-size: 17px;
  }

  .back-brand {
    width: 370px; display: flex; align-items: center; justify-content: center;
  }
  .back-brand .wordmark { color: var(--logo-green); font-size: 26px; }
  .back-brand .wordmark-square { background: var(--logo-green); width: 18px; height: 18px; }

  .back-rule { width: 8px; background: var(--paper); border-left: 4px solid var(--leaf); }

  .back-details {
    flex: 1; background: var(--forest); color: var(--ink-light);
    padding: 74px 0 0 36px; font-size: 15px; line-height: 1.35;
  }
  .person-name { color: var(--leaf); font-weight: 600; font-size: 21px; }
  .person-role { margin-bottom: 18px; }
  .address { margin-bottom: 16px; }
  .contact-list { list-style: none; }
  .contact-list li { display: flex; align-items: center; gap: 8px; }
  .contact-list svg { width: 13px; height: 13px; flex: none; fill: var(--leaf); }
</style>
</head>
<body>
  <section class="card card-front" aria-label="Card front">
    <div class="wordmark"><span class="wordmark-square"></span>Lumenway Retrofit Group</div>
    <p class="front-web">www.yourweb.com</p>
  </section>

  <section class="card card-back" aria-label="Card back">
    <div class="back-brand">
      <div class="wordmark"><span class="wordmark-square"></span>Lumenway Retrofit Group</div>
    </div>
    <div class="back-rule"></div>
    <div class="back-details">
      <p class="person-name">John Smith</p>
      <p class="person-role">President</p>
      <p class="address">Street Name Ave, Suite 100<br>State, Zip Code, Country</p>
      <ul class="contact-list">
        <li><svg viewBox="0 0 16 16"><path d="M3 1l3 3-2 2c1 2 3 4 5 5l2-2 3 3-2 3C6 15 1 10 0 4z"/></svg>01 012-345-6789</li>
        <li><svg viewBox="0 0 16 16"><path d="M4 0h8v16H4zM5.5 2v10h5V2z"/></svg>01 012-345-6780</li>
        <li><svg viewBox="0 0 16 16"><path d="M0 3h16v10H0zM1.5 4.5 8 9l6.5-4.5v-.2H1.5z"/></svg>info@yourwebsite.com</li>
        <li><svg viewBox="0 0 16 16"><path d="M8 0a8 8 0 1 0 0 16A8 8 0 0 0 8 0zm0 1.5a6.5 6.5 0 1 1 0 13 6.5 6.5 0 0 1 0-13zM2 7.3h12v1.4H2zM7.3 1.5h1.4v13H7.3z"/></svg>yourwebsite.com</li>
      </ul>
    </div>
  </section>
</body>
</html>
```